Harborline Auto LLC

Car Dealer Customer Service
Address: 2874 Cresthaven Road, Shelbyville, TN 37162
web: www.harborlineautoxq.net
email: harborlineautoxq@mailnest.example
Phone: (931) 555-0148
Phone: (629) 555-0173

```html
<!DOCTYPE html>
<html lang="en">
<head>
<meta charset="utf-8">
<title>Harborline Auto – Business Card</title>
<link rel="stylesheet" href="https://fonts.googleapis.com/css2?family=Montserrat:wght@700&family=Mulish:wght@500&display=swap">
<style>
  :root {
    --stage: #333333;
    --front-blue: #1d7aad;
    --back-blue: #2890c9;
    --brand-blue: #2479ab;
    --gold: #ebb144;
    --white: #ffffff;
  }
  * { margin: 0; padding: 0; box-sizing: border-box; }
  html, body { width: 1200px; height: 984px; overflow: hidden; background: var(--stage); }
  .canvas { position: relative; width: 1200px; height: 984px; }
  .card {
    position: absolute; left: 220px; width: 760px; height: 434px;
    overflow: hidden; box-shadow: 0 10px 24px rgba(0,0,0,.45);
  }
  .card--front { top: 38px; background: var(--front-blue); }
  .card--back { top: 512px; background: var(--white); }

  .brand { position: absolute; display: flex; align-items: center; gap: 14px;
    font-family: "Montserrat", sans-serif; font-weight: 700; letter-spacing: .02em; text-transform: uppercase; white-space: nowrap; }
  .brand__dot { border-radius: 50%; background: var(--gold); flex: none; }
  .card--front .brand { left: 50%; top: 50%; transform: translate(-50%,-50%); color: var(--white); font-size: 44px; }
  .card--front .brand__dot { width: 44px; height: 44px; }
  .card--back .brand { left: 575px; top: 250px; transform: translate(-50%,-50%); color: var(--brand-blue); font-size: 26px; }
  .card--back .brand__dot { width: 26px; height: 26px; }

  .wave { position: absolute; inset: 0; }
  .contact { position: absolute; left: 48px; top: 92px; color: var(--white);
    font-family: "Mulish", sans-serif; font-weight: 500; font-size: 16px; line-height: 1.45; }
  .contact__role { margin-bottom: 4px; font-size: 17px; }
  .contact__list { list-style: none; margin-top: 8px; }
  .contact__item { display: flex; align-items: center; gap: 10px; }
  .contact__icon { width: 15px; height: 15px; flex: none; fill: var(--gold); }
</style>
</head>
<body>
<main class="canvas">
  <section class="card card--front" aria-label="Card front">
    <div class="brand"><span class="brand__dot"></span><span>Harborline Auto</span></div>
  </section>

  <section class="card card--back" aria-label="Card back">
    <svg class="wave" viewBox="0 0 760 434" width="760" height="434" aria-hidden="true">
      <path d="M0 0 H448 C395 100 402 180 420 260 C438 340 430 392 362 434 H0 Z" fill="var(--gold)"/>
      <path d="M0 0 H404 C335 80 332 160 360 258 C382 334 380 392 340 434 H0 Z" fill="var(--back-blue)" stroke="var(--white)" stroke-width="7"/>
    </svg>

    <div class="contact">
      <p class="contact__role">Car Dealer Customer Service</p>
      <p>2874 Cresthaven Road,<br>Shelbyville, TN 37162</p>
      <ul class="contact__list">
        <li class="contact__item">
          <svg class="contact__icon" viewBox="0 0 24 24"><path d="M6.6 10.8a15 15 0 0 0 6.6 6.6l2.2-2.2c.3-.3.7-.4 1-.2 1.1.4 2.3.6 3.6.6.6 0 1 .4 1 1V20c0 .6-.4 1-1 1A17 17 0 0 1 3 4c0-.6.4-1 1-1h3.5c.6 0 1 .4 1 1 0 1.3.2 2.5.6 3.6.1.3 0 .7-.2 1z"/></svg>
          <span>(931) 555-0148</span>
        </li>
        <li class="contact__item">
          <svg class="contact__icon" viewBox="0 0 24 24"><path d="M3 8c0-2 4-4 9-4s9 2 9 4v2h-5V8H8v2H3zM6 12h12l2 8H4z"/></svg>
          <span>(629) 555-0173</span>
        </li>
        <li class="contact__item">
          <svg class="contact__icon" viewBox="0 0 24 24"><path d="M2 5h20v14H2z M2 5l10 8 10-8" fill="var(--gold)" stroke="var(--back-blue)" stroke-width="1.5"/></svg>
          <span>harborlineautoxq@mailnest.example</span>
        </li>
        <li class="contact__item">
          <svg class="contact__icon" viewBox="0 0 24 24"><circle cx="12" cy="12" r="10"/><path d="M2 12h20M12 2c3 3 3 17 0 20M12 2c-3 3-3 17 0 20" fill="none" stroke="var(--back-blue)" stroke-width="1.3"/></svg>
          <span>www.harborlineautoxq.net</span>
        </li>
      </ul>
    </div>

    <div class="brand"><span class="brand__dot"></span><span>Harborline Auto</span></div>
  </section>
</main>
</body>
</html>
```